Business Cards Design for the electrical wholesaler: clean bold dynamic :)

We need a business card design that would follow our latest brand guidelines. As an electrical wholesaler we want to bring a fresh look and feel into the industry. The design should be clean bold and dynamic. It should come alive with the renewed energy of our green colour. Our grey colour should keep things balanced and complement the notion of maturity and responsibility. We employ Lato as a corporate font however are not bound by this font and we’re open to interpretation here.

Target Market(s)

Electrical contractors

Industry/Entity Type

Business

Contact Information for Business Card

Logo
Name & Surname: Halyna Dorosh
Job Title: Director of Marketing
Email: halya.dorosh@quillmail.example
Cell phone: XXX.XXX.XXXX
Address: 20517 - 87 Ave. Edmonton, AB, Canada. T6K 4N8
Business Phone: 780.555.0184
Website: www.brovix.example

Font styles to use
Other font styles liked:
• Lato

Requirements
Must have
• Logo & website
Nice to have
• Brand elements - some of them you may find in the attached Brand Guidelines (e.g. three lines on the background signifying "W")

```html
<!DOCTYPE html>
<html lang="en">
<head>
<meta charset="utf-8">
<title>Brovix business cards</title>
<link rel="stylesheet" href="https://fonts.googleapis.com/css2?family=Lato:wght@400;700&display=swap">
<style>
  :root {
    --brand-green: #8dc63f;
    --brand-grey: #58595b;
    --text-dark: #4e4f51;
    --text-soft: #77787a;
    --rule: #6d6e70;
    --card: #ffffff;
    --backdrop: #e6e8eb;
  }
  * { box-sizing: border-box; margin: 0; padding: 0; }
  html, body { width: 1200px; height: 1000px; overflow: hidden; }
  body {
    position: relative;
    background: var(--backdrop);
    font-family: "Lato", Arial, sans-serif;
    color: var(--text-dark);
  }
  .card {
    position: absolute;
    background: var(--card);
  }
  .card--rounded { border-radius: 28px; }
  .card--a { left: 64px; top: 60px; width: 508px; height: 290px; }
  .card--b { left: 64px; top: 428px; width: 508px; height: 289px; }
  .card--c { left: 624px; top: 282px; width: 512px; height: 292px; }
  .card--d { left: 624px; top: 639px; width: 512px; height: 292px; }

  .wordmark {
    display: flex;
    align-items: center;
    gap: 12px;
    font-weight: 700;
    color: var(--brand-grey);
    line-height: 1;
    letter-spacing: -0.5px;
  }
  .wordmark__dot {
    border-radius: 50%;
    background: var(--brand-green);
    flex: none;
  }
  .card__front-mark {
    position: absolute;
    inset: 0;
    display: flex;
    align-items: center;
    justify-content: center;
  }
  .card__front-mark .wordmark { font-size: 64px; }
  .card__front-mark .wordmark__dot { width: 40px; height: 40px; }

  .card__corner-mark {
    position: absolute;
    right: 30px;
    top: 26px;
  }
  .card__corner-mark .wordmark { font-size: 42px; gap: 9px; }
  .card__corner-mark .wordmark__dot { width: 26px; height: 26px; }

  .person { position: absolute; left: 27px; top: 94px; }
  .person__name { font-size: 26px; font-weight: 400; color: var(--text-dark); }
  .person__title { font-size: 15px; color: var(--text-soft); margin-top: 2px; }

  .divider {
    position: absolute;
    left: 224px; right: 30px; top: 143px;
    height: 2px;
    background: var(--rule);
  }
  .address {
    position: absolute;
    right: 30px; top: 154px;
    font-size: 15px;
    line-height: 19px;
    text-align: right;
    color: var(--text-soft);
  }
  .address__pin {
    display: inline-block;
    width: 10px; height: 14px;
    margin-right: 14px;
    vertical-align: -1px;
  }
  .contacts { position: absolute; left: 28px; top: 196px; list-style: none; }
  .contacts__item {
    display: flex;
    align-items: center;
    font-size: 17px;
    line-height: 24px;
    color: var(--text-dark);
  }
  .contacts__icon { width: 13px; height: 13px; margin-right: 12px; flex: none; }
  .website {
    position: absolute;
    right: 30px; top: 242px;
    font-size: 15px;
    color: var(--text-soft);
  }
  svg path, svg rect, svg circle { fill: var(--brand-grey); }
</style>
</head>
<body>

  <section class="card card--rounded card--a" aria-label="Card front, rounded">
    <div class="card__front-mark">
      <div class="wordmark"><span class="wordmark__dot"></span>brovix</div>
    </div>
  </section>

  <section class="card card--rounded card--b" aria-label="Card back, rounded">
    <div class="card__corner-mark">
      <div class="wordmark"><span class="wordmark__dot"></span>brovix</div>
    </div>
    <div class="person">
      <h1 class="person__name">Halyna Dorosh</h1>
      <p class="person__title">Director of Marketing</p>
    </div>
    <div class="divider"></div>
    <p class="address">
      <svg class="address__pin" viewBox="0 0 10 14"><path d="M5 0a5 5 0 0 0-5 5c0 3.6 5 9 5 9s5-5.4 5-9a5 5 0 0 0-5-5zm0 7a2 2 0 1 1 0-4 2 2 0 0 1 0 4z"/></svg>20517 - 87 Ave. Edmonton<br>AB, Canada. T6K 4N8
    </p>
    <ul class="contacts">
      <li class="contacts__item"><svg class="contacts__icon" viewBox="0 0 14 14"><path d="M3 0l2.4 3.2-1.3 1.6c.8 1.9 2.3 3.4 4.2 4.2l1.6-1.3L13 10v2.2c0 1-1 1.8-2 1.6C5.5 12.9 1.1 8.5.2 3 0 2 .8 1 1.8 1z"/></svg>780.555.0184</li>
      <li class="contacts__item"><svg class="contacts__icon" viewBox="0 0 14 14"><path d="M7 2C3.5 2 .5 3 0 5v2h3.5V5.5C4.5 5 5.7 4.8 7 4.8s2.5.2 3.5.7V7H14V5c-.5-2-3.5-3-7-3zM3 8l-1 5h10l-1-5zm4 1.2a1.6 1.6 0 1 1 0 3.2 1.6 1.6 0 0 1 0-3.2z"/></svg>780.555.0184</li>
      <li class="contacts__item"><svg class="contacts__icon" viewBox="0 0 14 14"><path d="M0 3h14v1.2L7 8.5 0 4.2zm0 2.6l7 4.3 7-4.3V11H0z"/></svg>halya.dorosh@quillmail.example</li>
    </ul>
    <p class="website">www.brovix.example</p>
  </section>

  <section class="card card--c" aria-label="Card front, square">
    <div class="card__front-mark">
      <div class="wordmark"><span class="wordmark__dot"></span>brovix</div>
    </div>
  </section>

  <section class="card card--d" aria-label="Card back, square">
    <div class="card__corner-mark">
      <div class="wordmark"><span class="wordmark__dot"></span>brovix</div>
    </div>
    <div class="person">
      <h2 class="person__name">Halyna Dorosh</h2>
      <p class="person__title">Director of Marketing</p>
    </div>
    <div class="divider"></div>
    <p class="address">
      <svg class="address__pin" viewBox="0 0 10 14"><path d="M5 0a5 5 0 0 0-5 5c0 3.6 5 9 5 9s5-5.4 5-9a5 5 0 0 0-5-5zm0 7a2 2 0 1 1 0-4 2 2 0 0 1 0 4z"/></svg>20517 - 87 Ave. Edmonton<br>AB, Canada. T6K 4N8
    </p>
    <ul class="contacts">
      <li class="contacts__item"><svg class="contacts__icon" viewBox="0 0 14 14"><path d="M3 0l2.4 3.2-1.3 1.6c.8 1.9 2.3 3.4 4.2 4.2l1.6-1.3L13 10v2.2c0 1-1 1.8-2 1.6C5.5 12.9 1.1 8.5.2 3 0 2 .8 1 1.8 1z"/></svg>780.555.0184</li>
      <li class="contacts__item"><svg class="contacts__icon" viewBox="0 0 14 14"><path d="M7 2C3.5 2 .5 3 0 5v2h3.5V5.5C4.5 5 5.7 4.8 7 4.8s2.5.2 3.5.7V7H14V5c-.5-2-3.5-3-7-3zM3 8l-1 5h10l-1-5zm4 1.2a1.6 1.6 0 1 1 0 3.2 1.6 1.6 0 0 1 0-3.2z"/></svg>780.555.0184</li>
      <li class="contacts__item"><svg class="contacts__icon" viewBox="0 0 14 14"><path d="M0 3h14v1.2L7 8.5 0 4.2zm0 2.6l7 4.3 7-4.3V11H0z"/></svg>halya.dorosh@quillmail.example</li>
    </ul>
    <p class="website">www.brovix.example</p>
  </section>

</body>
</html>
```